Website for Torvel Capital - investment banking firm

We have a corporate identity (thanks to Ravinka/31842) and want to extend that into a website design.  See the attached zipped files.
We have software folks in-house to do the coding.
See the attached Project Brief & Notes for more details.  Don't worry about the actual text - lorem ipsum will be fine.
The server will be Apache.
Thank you!
Desmond

Industry/Entity Type
Investment

```html
<!DOCTYPE html>
<html lang="en">
<head>
<meta charset="utf-8">
<title>Torvel Capital</title>
<link href="https://fonts.googleapis.com/css2?family=Open+Sans:wght@400;600;700&family=Raleway:wght@400;500;600&display=swap" rel="stylesheet">
<style>
:root{
  --ink:#2b2b2b;
  --muted:#8a8a8a;
  --text:#555;
  --blue:#3a78d4;
  --navy:#24509a;
  --navy-dark:#1b3d78;
  --hero-box:#0c1a22;
  --footer:#2e2e2e;
  --footer-bottom:#141414;
  --rule:#e4e4e4;
  --field:#ececec;
}
*{box-sizing:border-box;margin:0;padding:0}
html,body{width:787px;height:1200px;overflow:hidden;background:#fff}
body{position:relative;font-family:"Open Sans",Arial,sans-serif;color:var(--text)}
a{text-decoration:none;color:inherit}
.abs{position:absolute}

/* header */
.site-header{position:absolute;left:0;top:0;width:787px;height:81px;border-top:2px solid #333;background:#fff}
.brand{position:absolute;left:72px;top:26px;display:flex;align-items:center;gap:8px}
.brand-mark{width:18px;height:18px;background:var(--navy)}
.brand-name{font-family:"Raleway",sans-serif;font-size:19px;font-weight:500;color:var(--navy);letter-spacing:.5px}
.main-nav{position:absolute;top:0;left:374px;height:79px;display:flex;font-size:8.5px;color:#666}
.main-nav a{display:flex;align-items:center;padding:0 9px;height:79px}
.main-nav a.active{background:#f4f4f4;color:var(--blue);border-top:2px solid var(--blue);width:42px;justify-content:center;padding:0}

/* hero */
.hero{position:absolute;left:0;top:81px;width:787px;height:341px;
  background:linear-gradient(90deg,#c9d6de 0%,#b4c4cf 35%,#d7dee3 60%,#c3cfd8 100%)}
.hero-card{position:absolute;left:71px;top:87px;width:305px;height:172px;background:var(--hero-box);padding:11px 14px}
.hero-card h1{font-family:"Raleway",sans-serif;font-weight:500;color:#fff;font-size:19px;line-height:26px}
.hero-card p{color:#dfe5ea;font-size:10.5px;line-height:16px;margin-top:6px}
.btn-hero{position:absolute;left:15px;top:132px;width:124px;height:29px;background:var(--blue);color:#fff;
  font-family:"Raleway",sans-serif;font-size:12px;display:flex;align-items:center;justify-content:center}

/* intro columns */
.intro-col{position:absolute;top:464px;width:180px}
.intro-col h2{display:flex;align-items:center;gap:5px;font-family:"Raleway",sans-serif;font-weight:400;font-size:12.5px;color:var(--ink)}
.intro-col h2 svg{width:24px;height:24px}
.intro-col p{margin-top:14px;font-size:8px;line-height:13px;color:var(--muted)}
.learn{display:inline-block;margin-top:6px;font-size:8px;font-weight:700;color:var(--navy-dark);text-decoration:underline}

.shadow-rule{position:absolute;left:56px;top:606px;width:675px;height:8px;
  background:radial-gradient(ellipse at top,rgba(0,0,0,.12),rgba(0,0,0,0) 70%)}

.global{position:absolute;left:0;top:644px;width:787px;text-align:center}
.global h2{font-family:"Raleway",sans-serif;font-weight:400;font-size:16px;color:#333}
.global p{font-size:8px;line-height:14.5px;color:#777;margin-top:8px}
.btn{display:flex;align-items:center;justify-content:center;background:var(--navy);color:#fff;
  font-family:"Raleway",sans-serif;font-size:10px;border-bottom:2px solid var(--navy-dark)}
.global .btn{margin:15px auto 0;width:102px;height:24px}
.rule{position:absolute;left:72px;top:764px;width:643px;height:1px;background:var(--rule)}

/* lower */
.block{position:absolute;top:804px}
.block h3{font-family:"Raleway",sans-serif;font-weight:400;color:#333;font-size:14px;padding-bottom:8px;border-bottom:1px solid var(--rule)}
.block h3 small{font-size:8.5px;color:#444}
.positioning{left:72px;width:284px}
.positioning h3{font-size:16px;padding-bottom:6px}
.positioning p{font-size:8px;line-height:13px;color:#666;margin-top:10px}
.positioning p + p{margin-top:7px}
.tweets{left:370px;width:163px}
.tweet{font-size:8px;line-height:13px;color:#555;padding:7px 0 5px;border-bottom:1px solid var(--rule)}
.tweet:last-of-type{border-bottom:0}
.tweet a{color:var(--navy)}
.newsletter{left:552px;width:163px}
.newsletter p{font-size:8px;line-height:13px;color:#666;margin-top:10px}
.newsletter .note{font-size:5px;color:#aaa;margin-top:0;line-height:8px}
.field{height:21px;background:var(--field);border:1px solid #ddd;font-size:7px;color:#999;padding:6px 7px;margin-top:11px}
.field + .field{margin-top:10px}
.block .btn{position:absolute;top:150px;width:77px;height:21px}

/* footer */
.site-footer{position:absolute;left:0;top:1030px;width:787px;height:144px;background:var(--footer)}
.foot-col{position:absolute;top:22px}
.foot-col h4{font-family:"Raleway",sans-serif;font-weight:400;font-size:12px;color:#fff;margin-bottom:12px}
.foot-col li{list-style:none;font-size:7.5px;line-height:13px;color:#8d8d8d}
.foot-bottom{position:absolute;left:0;top:1174px;width:787px;height:26px;background:var(--footer-bottom);
  color:#ccc;font-size:8px;display:flex;align-items:center;justify-content:center}
</style>
</head>
<body>

<header class="site-header">
  <div class="brand"><span class="brand-mark"></span><span class="brand-name">Torvel Capital</span></div>
  <nav class="main-nav">
    <a class="active" href="#">Home</a>
    <a href="#">About</a>
    <a href="#">Services</a>
    <a href="#">Current Engagements</a>
    <a href="#">Completed Transactions</a>
  </nav>
</header>

<section class="hero" role="img" aria-label="Photo of a smiling businessman in a striped shirt in a bright office">
  <div class="hero-card">
    <h1>Torvel Capital, LLC Investment Banking Mergers &amp;Acquisitions</h1>
    <p>Sed ut perspiciatis unde omnis iste natus error sit totam Duis aute irure dolor in reprehenderit in voluptate velit esse cillum rem aperiam eaque ipsa quae ab illo.</p>
    <a class="btn-hero" href="#">Read More</a>
  </div>
</section>

<div class="intro-col" style="left:74px">
  <h2><svg viewBox="0 0 24 24"><circle cx="12" cy="12" r="12" fill="#222"/><text x="12" y="17" text-anchor="middle" font-family="Open Sans,sans-serif" font-weight="700" font-size="14" fill="#fff">?</text></svg>Who we are</h2>
  <p>Sed ut perspiciatis unde omnis iste natus error sit voluptatem accusantium doloremque laudantium, totam rem aperiam, eaque ipsa quae ab illo .</p>
  <a class="learn" href="#">Learn More</a>
</div>
<div class="intro-col" style="left:307px">
  <h2><svg viewBox="0 0 24 24"><circle cx="12" cy="12" r="12" fill="#222"/><rect x="7" y="7" width="10" height="10" fill="none" stroke="#fff" stroke-width="1.3"/><path d="M9 10h6M9 12h6M9 14h6" stroke="#fff" stroke-width="1"/></svg>What we do</h2>
  <p>Sed ut perspiciatis unde omnis iste natus error sit voluptatem accusantium doloremque laudantium, totam rem aperiam, eaque ipsa quae ab illo .</p>
  <a class="learn" href="#">Learn More</a>
</div>
<div class="intro-col" style="left:542px">
  <h2><svg viewBox="0 0 24 24"><circle cx="12" cy="12" r="12" fill="#222"/><circle cx="12" cy="12" r="3.5" fill="none" stroke="#fff" stroke-width="2.4" stroke-dasharray="1.6 1"/><circle cx="12" cy="12" r="1.2" fill="#222"/></svg>Our services</h2>
  <p>Sed ut perspiciatis unde omnis iste natus error sit voluptatem accusantium doloremque laudantium, totam rem aperiam, eaque ipsa quae ab illo .</p>
  <a class="learn" href="#">Learn More</a>
</div>

<div class="shadow-rule"></div>

<section class="global">
  <h2>Global Investment Banking Services</h2>
  <p>Lorem ipsum dolor sit amet, consectetur adipisicing elit, sed do eiusmod tempor incididunt ut labore et dolore magna aliqua.<br>Ut enim ad minim veniam, quis nostrud exercitation ullamco laboris nisi ut aliquip ex ea commodo consequat.</p>
  <a class="btn" href="#">Read More</a>
</section>

<div class="rule"></div>

<section class="block positioning">
  <h3>Positioning statement <small>Global, Professional, Trusted</small></h3>
  <p>Sed ut perspiciatis unde omnis iste natus error sit voluptatem accusantium doloremque laudantium, totam rem aperiam, eaque ipsa quae ab illo inventore veritatis et quasi architecto beatae vitae dicta sunt explicabo.</p>
  <p>qui dolorem ipsum quia dolor sit amet, consectetur, adipisci velit, sed quia non numquam eius modi tempora incidunt ut labore et dolore magnam aliquam quaerat voluptatem.</p>
  <a class="btn" href="#">Read More</a>
</section>

<section class="block tweets">
  <h3>Latest tweets</h3>
  <p class="tweet">Lorem ipsum dolor sit amet, consectetur adipisicing elit, <a href="#">sed do eiusmod tempor</a></p>
  <p class="tweet">Lorem ipsum dolor sit amet, consectetur adipisicing elit, <a href="#">sed do eiusmod tempor</a></p>
  <p class="tweet">Lorem ipsum dolor sit amet, consectetur adipisicing elit, <a href="#">sed do eiusmod tempor</a></p>
  <a class="btn" href="#">More info</a>
</section>

<section class="block newsletter">
  <h3>Subscribe to newsletter</h3>
  <p>Subscribe to our monthly newsletter to be updated with our new offers.</p>
  <p class="note">Your email address is safe and we also hate Spam</p>
  <div class="field">Name</div>
  <div class="field">Email</div>
  <a class="btn" href="#">Subscribe</a>
</section>

<footer class="site-footer">
  <div class="foot-col" style="left:72px"><h4>Site Linke</h4><ul><li>Home</li><li>About</li><li>Services</li><li>Current Engagements</li><li>Completed Transactions</li></ul></div>
  <div class="foot-col" style="left:235px"><h4>Company</h4><ul><li>About Crestline</li><li>Careers</li><li>Referral Program</li></ul></div>
  <div class="foot-col" style="left:369px"><h4>Resources</h4><ul><li>Blog</li><li>Articles</li><li>Webinars</li><li>Events</li><li>Downloads</li></ul></div>
  <div class="foot-col" style="left:499px"><h4>Features</h4><ul><li>Documentation</li><li>Scheduling</li><li>Practice Management</li><li>Billing</li><li>Compliance</li></ul></div>
  <div class="foot-col" style="left:631px"><h4>Contact us</h4><ul><li>Request A Free Demo</li><li>Contact Crestline</li><li>Phone: 866-555-0142</li><li>Fax: 866-555-0178</li></ul></div>
</footer>
<div class="foot-bottom">© Copyright 2014. All rights reseverd.</div>

</body>
</html>
```